New Mechanical Maintenance business needs website

New Mechanical Maintenance business in Perth Western Australia needs a nice and easy to navigate website. Showing what we do and how we can be the right fit for other small to medium size business by offering personalized service from our highly skilled team. We deal with both fixed plant repairs like food and chemical processing facilities to heavy equipment like drill rigs, Large boats and earthmoving equipment.

Target Market(s)

Small to medium business to offer personalized services/packages

Industry/Entity Type

e deal with both fixed plant repairs like food and chemical processing facilities to heavy equipment like drill rigs, Large boats and earthmoving equipment.

Coding

Coded - Design and coding required

Number of Pages Required

4 page

Font styles to use
Serif

Colors
0054AA
0677BA
7BADD7
CADEEF
E8F1F8

Requirements
Must have
• A website that is easy to navigate but covers off on the range of services/maintenance we can provide

```html
<!DOCTYPE html>
<html lang="en">
<head>
<meta charset="utf-8">
<title>Ridgeway Maintenance</title>
<link href="https://fonts.googleapis.com/css2?family=Source+Serif+4:wght@400;600;700&family=Montserrat:wght@400;500;600&display=swap" rel="stylesheet">
<style>
:root{
  --blue:#0054AA;
  --mid:#0677BA;
  --light:#7BADD7;
  --pale:#CADEEF;
  --mist:#E8F1F8;
  --ink:#1b1b1b;
  --white:#fff;
  --black:#000;
  --grey:#4a4f55;
}
*{margin:0;padding:0;box-sizing:border-box}
html,body{width:1200px;height:5072px;overflow:hidden}
body{font-family:"Source Serif 4",Georgia,serif;color:var(--ink);background:var(--white);position:relative}
.sans{font-family:"Montserrat",Arial,sans-serif}
section,header,footer{position:relative;width:1200px;overflow:hidden}
.abs{position:absolute}
.btn{position:absolute;display:flex;align-items:center;justify-content:center;border-radius:20px;font-weight:700;font-size:14px}
.btn-blue{background:var(--blue);color:var(--white)}
.btn-white{background:var(--white);color:var(--ink)}
h2{font-weight:700;font-size:38px;line-height:1.1}
h2 .accent{color:var(--blue)}
.ph{position:absolute}

/* header */
.site-header{height:173px;background:var(--white)}
.topbar{position:absolute;left:368px;top:0;width:832px;height:69px;background:var(--blue);clip-path:polygon(0 0,100% 0,100% 100%,40px 100%)}
.topbar-item{position:absolute;top:0;height:69px;display:flex;align-items:center;gap:14px;color:var(--white);font-size:13px;font-family:"Montserrat",sans-serif;white-space:nowrap}
.topbar-sep{position:absolute;top:0;width:1px;height:69px;border-left:1px dashed rgba(255,255,255,.6)}
.nav{position:absolute;top:112px;left:424px;font-family:"Montserrat",sans-serif;font-size:13px}
.nav a{position:absolute;white-space:nowrap;color:var(--ink);text-decoration:none}
.nav a.active{color:var(--blue);font-weight:600;border-bottom:2px solid var(--blue);padding-bottom:2px}
.logo-disc{position:absolute;left:112px;top:-20px;width:226px;height:226px;border-radius:50%;background:var(--white);z-index:3;display:flex;align-items:center;justify-content:center;text-align:center}
.brand{font-family:"Source Serif 4",serif;font-weight:700;color:var(--grey);font-size:24px;line-height:1.15;letter-spacing:1px}

/* hero */
.hero{height:615px}
.hero-art{inset:0;background:linear-gradient(100deg,#0b4d9c 0%,#1f66b0 35%,#7a7c92 60%,#c77a4a 78%,#2a4f7c 100%)}
.hero .welcome{position:absolute;left:113px;top:203px;font-size:28px;color:var(--white);font-weight:600;line-height:1.2}
.hero h1{position:absolute;left:108px;top:248px;font-size:50px;line-height:1.1;color:var(--white);font-weight:600;letter-spacing:.5px;white-space:nowrap}
.hero p{position:absolute;left:113px;top:323px;width:540px;font-size:13px;line-height:22px;color:var(--white)}

/* about */
.about{height:536px}
.about p{position:absolute;left:112px;width:450px;font-size:14.5px;line-height:26px;color:#222}

/* what we do */
.services{height:886px;background:linear-gradient(135deg,#0a56a8 0%,#1a74c0 45%,#0b5aad 100%)}
.services .intro{position:absolute;left:112px;top:158px;width:290px;font-size:14px;line-height:26px;color:var(--white);text-align:justify}
.svc-card{position:absolute;width:311px;height:342px;background:var(--white);clip-path:polygon(0 0,calc(100% - 34px) 0,100% 34px,100% 100%,0 100%)}
.svc-card .ph{left:8px;top:8px;width:295px;height:268px;clip-path:polygon(0 0,calc(100% - 30px) 0,100% 30px,100% 100%,0 100%)}
.svc-card .label{position:absolute;left:16px;bottom:18px;font-family:"Montserrat",sans-serif;font-size:17px;color:#222}

/* origins */
.origins{height:493px;background:var(--white)}
.origins li{position:absolute;left:630px;width:460px;list-style:none;display:flex;gap:14px;font-family:"Montserrat",sans-serif;font-size:13.5px;line-height:24px;color:#333;text-align:justify}
.origins li b{color:var(--mid);font-weight:600}

/* deals */
.deals{height:587px;background:linear-gradient(160deg,#0b58ac 0%,#0c4fa3 60%,#0a469a 100%);color:var(--white);text-align:center}
.deal-card{position:absolute;top:215px;width:310px;height:287px;overflow:hidden}
.deal-card .label{position:absolute;left:32px;bottom:30px;font-weight:700;font-size:19px;color:var(--white)}
.deal-feature{background:linear-gradient(160deg,#1a7cc4,#0a62b0);clip-path:polygon(0 0,calc(100% - 34px) 0,100% 34px,100% 100%,0 100%)}

/* testimonials */
.testimonials{height:522px}
.t-card{position:absolute;top:177px;width:495px;height:252px;background:var(--white);box-shadow:0 2px 10px rgba(0,0,0,.2)}
.t-card .ph{left:0;top:0;width:200px;height:252px}
.t-card .quote{position:absolute;left:226px;top:20px;font-size:40px;font-weight:700;line-height:1}
.t-card .name{position:absolute;left:229px;top:70px;color:var(--mid);font-size:16px}
.t-card .stars{position:absolute;right:30px;top:68px;color:#f2b818;font-size:12px;letter-spacing:1px}
.t-card p{position:absolute;left:229px;top:96px;width:245px;font-size:12px;line-height:22px;color:#333}
.t-card .more{position:absolute;left:236px;top:212px;font-size:11px;color:var(--blue)}
.arrow{position:absolute;top:3592px;width:28px;height:28px;border-radius:50%;border:1px solid #bbb;background:var(--white);display:flex;align-items:center;justify-content:center}

/* contact */
.contact{height:508px;background:linear-gradient(135deg,#0b57a8,#0e4a9d 50%,#0b56aa)}
.contact h2{text-align:center;color:var(--white);position:absolute;top:95px;width:100%}
.field{position:absolute;background:var(--white);border-radius:29px;height:58px;font-family:"Montserrat",sans-serif;font-size:14px;color:#333;padding-left:24px;display:flex;align-items:center}

/* newsletter */
.newsletter{height:392px;text-align:center}

/* footer */
.site-footer{height:360px;background:var(--black);color:var(--white)}
.fnav a{position:absolute;top:120px;color:var(--white);text-decoration:none;font-family:"Montserrat",sans-serif;font-size:13px;font-weight:600}
.fsep{position:absolute;top:118px;width:2px;height:20px;background:var(--white)}
.fcontact{position:absolute;top:190px;display:flex;align-items:center;gap:16px;font-size:13px;letter-spacing:.5px;white-space:nowrap}
.social{position:absolute;top:325px;width:22px;height:22px;border-radius:50%;background:var(--white)}
</style>
</head>
<body>

<header class="site-header">
  <div class="topbar">
    <div class="topbar-item" style="left:60px">
      <svg width="18" height="22" viewBox="0 0 18 22"><path d="M9 1a7 7 0 0 0-7 7c0 5 7 13 7 13s7-8 7-13a7 7 0 0 0-7-7z" fill="none" stroke="#fff" stroke-width="2"/><circle cx="9" cy="8" r="2.6" fill="#fff"/></svg>
      12 Kent Way, Perth WA 6000
    </div>
    <div class="topbar-sep" style="left:330px"></div>
    <div class="topbar-item" style="left:356px">
      <svg width="18" height="18" viewBox="0 0 24 24"><path d="M6.6 10.8a15 15 0 0 0 6.6 6.6l2.2-2.2c.3-.3.7-.4 1-.2 1.1.4 2.3.6 3.6.6.6 0 1 .4 1 1V20c0 .6-.4 1-1 1A17 17 0 0 1 3 4c0-.6.4-1 1-1h3.5c.6 0 1 .4 1 1 0 1.3.2 2.5.6 3.6.1.3 0 .7-.2 1z" fill="#fff"/></svg>
      +61 8 5550 1234
    </div>
    <div class="topbar-sep" style="left:540px"></div>
    <div class="topbar-item" style="left:566px">
      <svg width="20" height="14" viewBox="0 0 20 14"><rect x="1" y="1" width="18" height="12" fill="none" stroke="#fff" stroke-width="1.6"/><path d="M1 1l9 7 9-7" fill="none" stroke="#fff" stroke-width="1.6"/></svg>
      info@ridgewaymaint.example
    </div>
  </div>
  <div class="logo-disc"><div class="brand">RIDGEWAY<br>MAINTENANCE</div></div>
  <nav class="nav">
    <a class="active" style="left:0">Home</a>
    <a style="left:82px">About Us</a>
    <a style="left:186px">What We Do</a>
    <a style="left:314px">Blog</a>
    <a style="left:384px">Testimonials</a>
  </nav>
  <div class="btn btn-blue" style="left:962px;top:106px;width:120px;height:38px;font-size:13px">Contact Us</div>
</header>

<section class="hero">
  <div class="ph hero-art" role="img" aria-label="Engineer in hard hat and high-visibility vest reviewing plans in front of an industrial plant at dusk"></div>
  <div class="welcome">Welcome To</div>
  <h1>RIDGEWAY MAINTENANCE</h1>
  <p>Lorem ipsum dolor sit amet, consectetur adipiscing elit, sed do eiusmod tempor incididunt ut labore et dolore magna aliqua. Ut enim ad minim veniam, quis nostrud</p>
  <div class="btn btn-white" style="left:111px;top:393px;width:122px;height:36px">Contact Us</div>
</section>

<section class="about">
  <h2 class="abs" style="left:112px;top:82px">About <span class="accent">Us</span></h2>
  <p style="top:150px">Lorem ipsum dolor sit amet, consectetur adipiscing elit, sed do eiusmod tempor incididunt ut labore et dolore magna aliqua. Ut enim ad minim veniam, quis nostrud exercitation ullamco laboris nisi ut aliquip ex ea commodo consequat.</p>
  <p style="top:266px">Duis aute irure dolor in reprehenderit in voluptate velit esse cillum dolore eu fugiat nulla pariatur. Excepteur sint occaecat cupidatat non proident, sunt in culpa qui officia deserunt mollit anim id est laborum."</p>
  <div class="btn btn-blue" style="left:111px;top:384px;width:122px;height:36px">Read More</div>
  <div class="ph" style="left:599px;top:87px;width:601px;height:362px;background:linear-gradient(120deg,#1d3a5c,#3f6f9a 50%,#1b2c44)" role="img" aria-label="Two mechanics working on an engine assembly in a workshop"></div>
</section>

<section class="services">
  <h2 class="abs" style="left:112px;top:100px;color:#fff">What We Do</h2>
  <p class="intro sans">Lorem ipsum dolor sit amet, consectetur adipiscing elit, sed do eiusmod tempor incididunt ut labore et dolore magna aliqua. Ut enim ad minim veniam, quis nostrud exercitation ullamco laboris nisi ut aliquip ex ea commodo consequat.</p>
  <div class="btn btn-white" style="left:112px;top:348px;width:122px;height:36px">Read More</div>

  <div class="svc-card" style="left:445px;top:88px"><div class="ph" style="background:linear-gradient(160deg,#5b6470,#2c3440)" role="img" aria-label="Rows of industrial machinery in a fixed plant"></div><div class="label">Plant Mechanics -Fixed</div></div>
  <div class="svc-card" style="left:768px;top:88px"><div class="ph" style="background:linear-gradient(160deg,#2c3a55,#151a24 70%,#6b5520)" role="img" aria-label="Excavator and dump truck working at night"></div><div class="label">Plant Mechanics - Fixed</div></div>
  <div class="svc-card" style="left:114px;top:455px"><div class="ph" style="background:linear-gradient(160deg,#9fb0bf,#3b5c86)" role="img" aria-label="Blue pumps and pipework in a processing facility"></div><div class="label">Pump installation and repairs</div></div>
  <div class="svc-card" style="left:445px;top:455px"><div class="ph" style="background:linear-gradient(160deg,#4e5560,#8e8a7a 60%,#2c3038)" role="img" aria-label="Gloved hands measuring a machined metal part"></div><div class="label">Open Cut Mining</div></div>
  <div class="svc-card" style="left:768px;top:455px"><div class="ph" style="background:linear-gradient(160deg,#6c6f74,#a9a6a0 50%,#3a3d42)" role="img" aria-label="Drill rig machinery with red hydraulic fittings"></div><div class="label">Drill Rigs</div></div>
</section>

<section class="origins">
  <div class="abs brand" style="left:115px;top:190px;width:360px;font-size:40px;line-height:1.2;text-align:center">RIDGEWAY<br>MAINTENANCE</div>
  <h2 class="abs" style="left:628px;top:80px">Where We <span class="accent">Come From</span></h2>
  <ul>
    <li style="top:152px"><svg width="20" height="18" viewBox="0 0 20 18" style="flex:none;margin-top:4px"><path d="M2 9l6 6L18 2" fill="none" stroke="#0054AA" stroke-width="3"/></svg><span>Director of the company has over <b>20-year experience</b> in the fixed and mobile plant industries ranging from <b>Perth local and overseas.</b></span></li>
    <li style="top:237px"><svg width="20" height="18" viewBox="0 0 20 18" style="flex:none;margin-top:4px"><path d="M2 9l6 6L18 2" fill="none" stroke="#0054AA" stroke-width="3"/></svg><span>Facilities like precious metals refining, offshore drilling and production platform,open cut and underground mining, civils, geotechnical and construction equipment and large-scale construction as an expat overseas.</span></li>
  </ul>
  <div class="btn btn-blue" style="left:630px;top:363px;width:122px;height:36px">Read More</div>
</section>

<section class="deals">
  <h2 class="abs" style="left:0;top:65px;width:100%;color:#fff">Our Deals</h2>
  <div class="abs" style="left:0;top:132px;width:100%;font-size:18px;font-weight:600">We deal with both fixed plant repairs and chemical processing</div>
  <div class="deal-card" style="left:114px"><div class="ph" style="inset:0;background:linear-gradient(180deg,#5a6a7e,#23456f 60%,#0d4f9e)" role="img" aria-label="Technician in hard hat inspecting pipework on a drill rig"></div><div class="label">Drill Rigs Repair</div></div>
  <div class="deal-card" style="left:447px;clip-path:polygon(0 0,calc(100% - 34px) 0,100% 34px,100% 100%,0 100%)"><div class="ph" style="inset:0;background:linear-gradient(180deg,#6e5a6a,#3a3e4a 60%,#0d4f9e)" role="img" aria-label="Worker servicing a boat propeller"></div><div class="label">Large Boats Equipment</div></div>
  <div class="deal-card deal-feature" style="left:778px">
    <div class="abs" style="left:0;top:58px;width:100%;font-size:19px;font-weight:700">Earthmoving Equipment</div>
    <div class="abs" style="left:35px;top:105px;width:240px;font-size:13px;line-height:25px">Lorem ipsum dolor sit amet, consectetur adipiscing elit, sed do eiusmod tempor incididunt ut labore et dolore magna aliqua.</div>
    <div class="abs" style="left:0;top:222px;width:100%;font-size:13px;text-decoration:underline">Read More...</div>
  </div>
</section>

<section class="testimonials">
  <h2 class="abs" style="left:0;top:80px;width:100%;text-align:center">Our <span class="accent">Testimonials</span></h2>
  <div class="t-card" style="left:98px">
    <div class="ph" style="background:linear-gradient(180deg,#d9d6d2,#b9b2aa)" role="img" aria-label="Portrait of a smiling client with arms crossed"></div>
    <div class="quote">&ldquo;</div><div class="name">Maren Ellis</div><div class="stars">★★★★★</div>
    <p>Lorem ipsum dolor sit amet, consectetur adipiscing elit, sed do eiusmod tempor incididunt ut labore et dolore magna aliqua. aute irure dolor in reprehenderit in voluptate .</p>
    <div class="more">Read More &nbsp;→</div>
  </div>
  <div class="t-card" style="left:607px">
    <div class="ph" style="background:linear-gradient(180deg,#5d6a78,#2e3846)" role="img" aria-label="Portrait of a client in a suit with arms crossed"></div>
    <div class="quote">&ldquo;</div><div class="name">Owen Tarrant</div><div class="stars">★★★★★</div>
    <p>Lorem ipsum dolor sit amet, consectetur adipiscing elit, sed do eiusmod tempor incididunt ut labore et dolore magna aliqua. aute irure dolor in reprehenderit in voluptate .</p>
    <div class="more">Read More &nbsp;→</div>
  </div>
</section>
<div class="arrow" style="left:38px"><svg width="12" height="10" viewBox="0 0 12 10"><path d="M11 5H1M5 1L1 5l4 4" fill="none" stroke="#333" stroke-width="1.5"/></svg></div>
<div class="arrow" style="left:1134px"><svg width="12" height="10" viewBox="0 0 12 10"><path d="M1 5h10M7 1l4 4-4 4" fill="none" stroke="#333" stroke-width="1.5"/></svg></div>

<section class="contact">
  <h2>Contact Us</h2>
  <div class="field" style="left:112px;top:183px;width:312px">Name</div>
  <div class="field" style="left:438px;top:183px;width:312px">Email</div>
  <div class="field" style="left:112px;top:260px;width:312px">Phone</div>
  <div class="field" style="left:438px;top:260px;width:312px">Subject</div>
  <div class="field" style="left:112px;top:337px;width:638px;justify-content:center;padding:0;font-weight:600">Send</div>
  <div class="field" style="left:765px;top:183px;width:323px;height:210px;border-radius:18px;align-items:flex-start;padding-top:20px">Message</div>
</section>

<section class="newsletter">
  <h2 class="abs" style="left:0;top:90px;width:100%;text-align:center">Newsletter <span class="accent">SignUp</span></h2>
  <p class="abs" style="left:230px;top:148px;width:740px;font-size:14px;line-height:25px;color:#222">Lorem ipsum dolor sit amet, consectetur adipiscing elit, sed do eiusmod tempor incididunt ut labore et dolore magna aliqua. Ut enim ad minim veniam, quis nostrud exercitation ullamco &nbsp;consequat.</p>
  <div class="abs" style="left:182px;top:226px;width:835px;height:74px;border-radius:37px;background:var(--white);box-shadow:0 2px 10px rgba(0,0,0,.18);overflow:hidden">
    <div class="abs" style="left:55px;top:0;height:74px;display:flex;align-items:center;font-size:14px">Enter Email Address</div>
    <div class="abs" style="right:0;top:0;width:185px;height:74px;background:var(--blue);color:#fff;display:flex;align-items:center;justify-content:center;font-weight:700;font-size:18px">Subscibe</div>
  </div>
</section>

<footer class="site-footer">
  <div class="abs" style="left:113px;top:85px;width:190px;height:160px;border-radius:80px;background:var(--white);display:flex;align-items:center;justify-content:center;text-align:center"><div class="brand" style="font-size:20px;color:#1b1b1b">RIDGEWAY<br>MAINTENANCE</div></div>
  <nav class="fnav">
    <a style="left:482px">Home</a><div class="fsep" style="left:550px"></div>
    <a style="left:565px">About Us</a><div class="fsep" style="left:655px"></div>
    <a style="left:670px">What We Do</a><div class="fsep" style="left:780px"></div>
    <a style="left:800px">Blog</a><div class="fsep" style="left:850px"></div>
    <a style="left:873px">Testimonials</a><div class="fsep" style="left:985px"></div>
    <a style="left:1003px">Contact Us</a>
  </nav>
  <div class="fcontact" style="left:422px"><svg width="26" height="26" viewBox="0 0 26 26"><circle cx="13" cy="13" r="13" fill="#fff"/><path d="M13 6a4.5 4.5 0 0 0-4.5 4.5c0 3.3 4.5 8.5 4.5 8.5s4.5-5.2 4.5-8.5A4.5 4.5 0 0 0 13 6z" fill="#000"/><circle cx="13" cy="10.5" r="1.7" fill="#fff"/></svg>12 Kent Way, Perth WA 6000</div>
  <div class="fcontact" style="left:702px"><svg width="26" height="26" viewBox="0 0 26 26"><circle cx="13" cy="13" r="13" fill="#fff"/><path d="M9.5 11.5a9 9 0 0 0 5 5l1.4-1.4c.2-.2.5-.3.7-.1.7.2 1.4.4 2.1.4.4 0 .6.2.6.6V18c0 .4-.2.6-.6.6A10.8 10.8 0 0 1 7.4 7.6c0-.4.2-.6.6-.6h2c.4 0 .6.2.6.6 0 .7.2 1.4.4 2.1.1.2 0 .5-.1.7z" fill="#000"/></svg>+61 8 5550 1234</div>
  <div class="fcontact" style="left:915px"><svg width="26" height="26" viewBox="0 0 26 26"><circle cx="13" cy="13" r="13" fill="#fff"/><rect x="7" y="8.5" width="12" height="9" fill="none" stroke="#000" stroke-width="1.5"/><path d="M7 8.5l6 5 6-5" fill="none" stroke="#000" stroke-width="1.5"/></svg>info@ridgewaymaint.example</div>
  <div class="abs" style="left:110px;top:300px;width:1050px;height:1px;background:#555"></div>
  <div class="social" style="left:120px"></div>
  <div class="social" style="left:148px"></div>
  <div class="social" style="left:176px"></div>
  <div class="social" style="left:204px"></div>
  <div class="abs" style="left:606px;top:328px;font-size:12px;letter-spacing:.4px">Copyright © 2024 &nbsp;Ridgeway Maintenance. All rights reserved. &nbsp;| &nbsp;<span class="sans">Privacy Policy</span></div>
</footer>

</body>
</html>
```